Core values in our company OKV (Residency and Relocation)

Do good:
1. Being Direct and communicative for the benefit of all parties
2. Working for the Benefit of the company, client and team members
3. Wanting to improve to create a better impact
4. Having healthy rivalry
Be ahead of curve:
1. Having the confidence to break through barriers which arise
2. Desire to grow and learn towards establishment and agreed goal
3. Getting off the sidelines and get into the game
4. Keeping the end game in mind having due regard to processes and milestones
5. Self starter and works on own initiative
6. Diligent and impactful in your field of responsibility
Truth and Honesty
2. Have the confidence and ability to speak what you really want to communicate
3. Being truthful to yourself, clients and colleagues to find the innovations that lie within
4. Seeking the truth by opening things up for discussion
5. Being Optimistic
Background Information on our Company:OKV is a professional law firm in London Docklands. We caters for both private and corporate clients ranging from highly regarded and established law firms to boutique and niche immigration practices. We also specialises in expert legal advice and prides itself on providing services that go beyond the expectations of its clients.
What we need: We need a Poster about Truth and Honesty, this is to show one of our values as a company. It will need to be vibrant and straight to the point. Colours can be orange grey white and yellow. Attached is our company logo.
Reason: To remind colleagues that this is one of our main values and it is instilled in our company.
Things we would like:
1. To create a point of focus
2. Use shapes to create visual interest
3. Use creative illustrations
4. Take the viewer’s focus on a journey with clever perspective
Industry/Entity Type
Legal
Requirements
Must have
- a globe (Picture)
- Do good:
- 1. Being Direct and communicative for the benefit of all parties
- 2. Working for the Benefit of the company, client and team members
- 3. Wanting to improve to create a better impact
- 4. Having healthy rivalry
- Be ahead of curve:
- 1. Having the confidence to break through barriers which arise
- 2. Desire to grow and learn towards establishment and agreed goal
- 3. Getting off the sidelines and get into the game
- 4. Keeping the end game in mind having due regard to processes and milestones
- 5. Self starter and works on own initiative
- 6. Diligent and impactful in your field of responsibility
- Truth and Honesty
- 2. Have the confidence and ability to speak what you really want to communicate
- 3. Being truthful to yourself, clients and colleagues to find the innovations that lie within
- 4. Seeking the truth by opening things up for discussion
- 5. Being Optimistic

```html
<!DOCTYPE html>
<html lang="en">
<head>
<meta charset="utf-8">
<title>OKV Core Values Poster</title>
<link rel="stylesheet" href="https://fonts.googleapis.com/css2?family=Noto+Serif:wght@400;700&family=Poppins:wght@500;600&display=swap">
<style>
  :root {
    --backdrop: #2b2b2b;
    --orange: #f07f1a;
    --yellow: #fdb913;
    --ink: #3a3a3a;
    --panel-light: #f4f4f4;
    --panel-mid: #dcdcdc;
    --footer: #3b3b3b;
    --white: #ffffff;
  }
  * { box-sizing: border-box; margin: 0; padding: 0; }
  html, body { width: 1200px; height: 2163px; overflow: hidden; }
  body { background: var(--backdrop); position: relative; font-family: "Poppins", sans-serif; }

  .poster { position: absolute; left: 50px; top: 304px; width: 1100px; height: 1555px; background: var(--white); overflow: hidden; }
  .shapes { position: absolute; inset: 0; }
  .hero-photo { position: absolute; left: 0; top: 0; width: 1100px; height: 661px;
    background: linear-gradient(180deg, #9fb1c2 0%, #c4ccd2 40%, #e2d6c8 70%, #8f8a88 100%); }

  .brand { position: absolute; left: 70px; top: 36px; display: flex; flex-direction: column; align-items: flex-start; }
  .brand-row { display: flex; align-items: center; gap: 14px; }
  .brand-mark { width: 26px; height: 26px; background: var(--orange); }
  .brand-name { font-family: "Noto Serif", serif; font-weight: 700; font-size: 78px; line-height: 1; color: var(--ink); }
  .brand-sub { font-family: "Noto Serif", serif; font-size: 18px; color: var(--ink); margin-top: 8px; }

  .headline { position: absolute; left: 50px; top: 760px; font-family: "Noto Serif", serif; color: var(--ink); line-height: 1; }
  .headline .the { font-size: 50px; display: block; }
  .headline .core { font-size: 68px; display: block; margin-top: 4px; }
  .headline .core b { font-weight: 700; }
  .headline .of { font-size: 86px; font-weight: 700; display: block; margin-top: 2px; }

  .tab { position: absolute; height: 66px; border-radius: 0 33px 33px 0;
    background: linear-gradient(90deg, var(--orange), var(--yellow));
    font-family: "Noto Serif", serif; font-weight: 700; font-size: 24px; color: var(--ink);
    display: flex; align-items: center; padding-left: 36px;
    box-shadow: 0 14px 10px -10px rgba(0,0,0,0.25); }
  .tab-truth { left: 0; top: 975px; width: 348px; }
  .tab-good { left: 483px; top: 682px; width: 350px; }
  .tab-curve { left: 483px: top: 0; }
  .tab-ahead { left: 483px; top: 982px; width: 350px; }

  .values { position: absolute; list-style: none; }
  .values li { position: relative; padding-left: 36px; font-weight: 600; font-size: 19px; line-height: 23px; color: var(--ink); }
  .values li::before { content: ""; position: absolute; left: 0; top: 3px; width: 16px; height: 16px; border: 2px solid var(--orange); border-radius: 50%; }
  .values li::after { content: ""; position: absolute; left: 6px; top: 6px; width: 4px; height: 8px; border: solid var(--orange); border-width: 0 2px 2px 0; transform: rotate(45deg); }
  .values-truth { left: 26px; top: 1075px; width: 440px; }
  .values-truth li { margin-bottom: 30px; text-align: justify; }
  .values-good { left: 510px; top: 772px; width: 560px; }
  .values-good li { margin-bottom: 20px; }
  .values-ahead { left: 510px; top: 1072px; width: 560px; }
  .values-ahead li { margin-bottom: 20px; }

  .footer-info { position: absolute; left: 470px; top: 1430px; width: 630px; display: flex; flex-direction: column; align-items: center; gap: 16px; }
  .site { display: flex; align-items: center; gap: 14px; font-family: "Noto Serif", serif; font-weight: 700; font-size: 28px; color: var(--white); }
  .social { display: flex; gap: 10px; }
  .social span { width: 38px; height: 38px; border: 2px solid var(--orange); border-radius: 50%; }
</style>
</head>
<body>
<main class="poster">
  <div class="hero-photo" role="img" aria-label="Photo of a hand in a suit pointing at sketched business diagrams over a hazy city skyline"></div>

  <svg class="shapes" width="1100" height="1555" viewBox="0 0 1100 1555" aria-hidden="true">
    <defs>
      <linearGradient id="panelFade" x1="0" y1="0" x2="1" y2="0">
        <stop offset="0" stop-color="#ececec"/>
        <stop offset="1" stop-color="#fafafa"/>
      </linearGradient>
    </defs>
    <!-- brand panel -->
    <path d="M0,0 H425 C452,0 455,22 446,48 L405,172 C396,196 384,204 360,204 H0 Z" fill="url(#panelFade)"/>
    <path d="M0,204 H360 C384,204 396,196 405,172 L446,48 C455,22 452,0 425,0 H1100" fill="none" stroke="var(--orange)" stroke-width="7"/>
    <!-- lower left panel -->
    <path d="M0,661 H470 V1400 C470,1470 430,1510 360,1525 L0,1555 Z" fill="url(#panelFade)"/>
    <!-- footer band -->
    <path d="M470,1420 H1100 V1555 H300 C400,1540 470,1500 470,1420 Z" fill="var(--footer)"/>
    <rect x="0" y="1535" width="1100" height="20" fill="var(--footer)"/>
  </svg>

  <div class="brand">
    <div class="brand-row">
      <span class="brand-mark"></span>
      <span class="brand-name">okv</span>
    </div>
    <span class="brand-sub">residency and relocation</span>
  </div>

  <h1 class="headline">
    <span class="the">THE</span>
    <span class="core">Core <b>Value</b></span>
    <span class="of">OF OKV</span>
  </h1>

  <div class="tab tab-truth">Truth and Honesty</div>
  <ul class="values values-truth">
    <li>Having the confidence to break through barriers which arise</li>
    <li>Have the confidence and ability to speak what you really want to communicate</li>
    <li>Being truthful to yourself, clients and colleagues to find the innovations that lie within</li>
    <li>Seeking the truth by opening things up for discussion</li>
    <li>Being Optimistic</li>
  </ul>

  <div class="tab tab-good">Do good:</div>
  <ul class="values values-good">
    <li>Being Direct and communicative for the benefit of all parties</li>
    <li>Working for the Benefit of the company, client and team members</li>
    <li>Wanting to improve to create a better impact</li>
    <li>Having healthy rivalry</li>
  </ul>

  <div class="tab tab-ahead">Be ahead of curve:</div>
  <ul class="values values-ahead">
    <li>Having the confidence to break through barriers which arise</li>
    <li>Desire to grow and learn towards establishment and agreed goal</li>
    <li>Getting off the sidelines and get into the game</li>
    <li>Keeping the end game in mind having due regard to processes and milestones</li>
    <li>Self starter and works on own initiative</li>
    <li>Diligent and impactful in your field of responsibility</li>
  </ul>

  <footer class="footer-info">
    <div class="site">
      <svg width="32" height="32" viewBox="0 0 32 32" aria-hidden="true">
        <g fill="none" stroke="var(--orange)" stroke-width="2">
          <circle cx="16" cy="16" r="14"/>
          <ellipse cx="16" cy="16" rx="6" ry="14"/>
          <line x1="2" y1="16" x2="30" y2="16"/>
          <path d="M5,8 H27 M5,24 H27"/>
        </g>
      </svg>
      www.residencyandrelocation.com
    </div>
    <div class="social" aria-hidden="true">
      <span></span><span></span><span></span><span></span><span></span><span></span><span></span><span></span>
    </div>
  </footer>
</main>
</body>
</html>
```